Business Card Design

We require a business card design for a law firm, our signature colours are maroon and cream. Our slogan is "From our family to yours", we would like the cards to be professional however feminine at the same time.

Industry/Entity Type

Business

Contact Information for Business Card

Helena Drace & Associates Lawyers & Conveyancers, Helena Drace LL.B. Principal Solicitor, 17 Kellow Street, Marrick NSW 2299

Logo styles of interest
Emblem Logo
Abstract Logo
Wordmark Logo

```html
<!DOCTYPE html>
<html lang="en">
<head>
<meta charset="utf-8">
<title>Helena Drace &amp; Associates – Business Card</title>
<link rel="stylesheet" href="https://fonts.googleapis.com/css2?family=Sorts+Mill+Goudy&family=Arimo:wght@400;700&display=swap">
<style>
  :root {
    --maroon: #741634;
    --maroon-deep: #5e0f29;
    --accent: #922e5e;
    --ink: #4b0a24;
    --cream: #f4e4a6;
    --cream-light: #f8ecbc;
    --glow: #fff3c4;
  }
  * { margin: 0; padding: 0; box-sizing: border-box; }
  html, body { width: 1200px; height: 741px; overflow: hidden; }
  body {
    position: relative;
    background: radial-gradient(ellipse at 50% 45%, var(--maroon) 0%, var(--maroon-deep) 100%);
  }
  .card {
    position: absolute;
    left: 108px; top: 119px;
    width: 986px; height: 499px;
    background: radial-gradient(ellipse at 45% 40%, var(--cream-light) 0%, var(--cream) 70%);
    border: 2px solid #3a1a1a;
    box-shadow: 0 0 22px 8px var(--glow);
  }
  .rule { position: absolute; background: var(--accent); }
  .bracket-top { left: 543px; top: 10px; width: 437px; height: 8px; }
  .bracket-right { left: 970px; top: 10px; width: 8px; height: 252px; }
  .bracket-left { left: 7px; top: 203px; width: 8px; height: 291px; }
  .bracket-bottom { left: 7px; top: 484px; width: 422px; height: 9px; }

  .firm {
    position: absolute;
    left: 27px;
    font-family: "Sorts Mill Goudy", "Goudy Old Style", serif;
    font-weight: 700;
    font-size: 49px;
    color: var(--ink);
    line-height: 1;
    text-shadow: 1px 2px 2px rgba(60, 10, 20, 0.45);
    letter-spacing: 0.2px;
  }
  .firm-name { top: 34px; }
  .firm-services { top: 94px; }
  .underline { position: absolute; height: 2px; background: var(--accent); }
  .firm-name-line { left: 27px; top: 86px; width: 700px; }
  .firm-services-line { left: 27px; top: 150px; width: 583px; }

  .emblem {
    position: absolute;
    left: 198px; top: 241px;
    width: 175px; height: 173px;
    border-radius: 8px;
    background: radial-gradient(ellipse at 50% 50%, #9a6f7c 0%, rgba(120, 60, 80, 0.35) 60%, rgba(244, 228, 166, 0) 100%);
  }

  .contact {
    position: absolute;
    left: 584px; top: 236px;
    font-family: "Arimo", Arial, sans-serif;
    color: var(--ink);
    line-height: 1;
  }
  .contact p { position: absolute; left: 0; white-space: nowrap; }
  .contact .name, .contact .role {
    font-weight: 700;
    font-size: 35px;
    letter-spacing: -0.6px;
    text-shadow: 1px 2px 2px rgba(60, 10, 20, 0.4);
  }
  .contact .name { top: 0; }
  .contact .role { top: 45px; }
  .contact .street, .contact .locality {
    font-size: 32px;
    letter-spacing: -0.2px;
    color: #3a0a1c;
  }
  .contact .street { top: 93px; }
  .contact .locality { top: 139px; }
  .contact-line { left: 584px; top: 456px; width: 311px; height: 3px; }
</style>
</head>
<body>
  <div class="card">
    <div class="rule bracket-top"></div>
    <div class="rule bracket-right"></div>
    <div class="rule bracket-left"></div>
    <div class="rule bracket-bottom"></div>

    <h1 class="firm firm-name">Helena Drace &amp; Associates</h1>
    <div class="underline firm-name-line"></div>
    <h2 class="firm firm-services">Lawyers &amp; Conveyancers</h2>
    <div class="underline firm-services-line"></div>

    <div class="emblem" role="img" aria-label="Ornamental scales of justice emblem in maroon with flourished base"></div>

    <address class="contact">
      <p class="name">Helena Drace LL.B</p>
      <p class="role">Principal Solicitor</p>
      <p class="street">17 Kellow Street,</p>
      <p class="locality">Marrick NSW 2299</p>
    </address>
    <div class="underline contact-line"></div>
  </div>
</body>
</html>
```